Webshop for furniture and lamps

We need a design for a web shop with APP that should have two options:
1-Webshop in general which should attract to private customer in general and
2-Website that is meant to attract big customers as hotels and restaurants who would have their own customerize login.

That's the idea behind the shop.

It should be diveded into 4 parts
vintage furniture
rattan set outdoor and indoor
lamps and
wooden wall decor

The name of the shop is loma vereda!

Please kindly make me an offer.

Reason: Dear designers, so far there hasn't been a design that really matched. Look up German web sites like www.glimmerhof-wohnen.de or www.sitzraum77.de... Haven't been convinced by designs! Sorry folks. Please submit some new ones. Kind regards Ned

```html
<!DOCTYPE html>
<html lang="en">
<head>
<meta charset="utf-8">
<title>loma vereda – furniture and lamps</title>
<link rel="stylesheet" href="https://fonts.googleapis.com/css2?family=Open+Sans:wght@400;600;700&family=Roboto:wght@400;500;700&display=swap">
<style>
:root{
  --orange:#f28a1c;
  --dark:#3b3b3b;
  --text:#333;
  --muted:#8a8a8a;
  --taupe:#b7ae9b;
  --page:#efeeea;
  --white:#fff;
  --line:#e4e2dc;
  --wood:#5b4130;
  --wood-dark:#3a2a20;
}
*{box-sizing:border-box;margin:0;padding:0}
html,body{width:1200px;height:2585px;overflow:hidden}
body{position:relative;background:var(--page);font-family:"Open Sans",Arial,sans-serif;color:var(--text);font-size:12px}
.abs{position:absolute}
a{color:inherit;text-decoration:none}

/* top bar */
.topbar{left:0;top:0;width:1200px;height:43px;background:var(--dark);color:#eee;font-size:12px;display:flex;align-items:center;justify-content:space-between;padding:0 93px}
.topbar .links{display:flex;gap:28px}
/* header */
.header{left:0;top:43px;width:1200px;height:103px;background:var(--white);display:flex;align-items:center;padding:0 93px}
.brand{display:flex;align-items:center;gap:12px;font-family:"Open Sans",sans-serif;font-weight:600;font-size:22px;color:var(--dark)}
.brand .mark{width:34px;height:34px;background:var(--dark)}
.nav{display:flex;gap:32px;margin-left:auto;font-family:Roboto,sans-serif;font-weight:500;font-size:13px;color:#222}
.search{margin-left:30px;width:230px;height:34px;border:1px solid #ddd;font-size:11px;color:#999;display:flex;align-items:center;justify-content:space-between;padding:0 12px 0 60px}

/* hero */
.hero{left:93px;top:185px;width:1016px;height:356px;background:linear-gradient(100deg,#8a6a52 0%,#b08a6a 30%,#6e5443 62%,#3e3430 100%)}
.hero-copy{position:absolute;left:676px;top:70px;width:300px;color:#fff}
.hero-copy h1{font-family:Roboto,sans-serif;font-weight:700;font-size:32px;letter-spacing:1px}
.hero-copy hr{border:0;border-top:1px solid rgba(255,255,255,.7);margin:14px 0 18px}
.hero-copy p{font-size:11.5px;line-height:19px;text-align:center}
.btn-light{display:inline-block;background:#fff;color:#222;font-weight:700;font-size:12px;padding:10px 16px;margin:26px 0 0 60px}

.box{background:var(--white)}
.box-title{font-family:Roboto,sans-serif;font-weight:700;font-size:17px;color:#222}

/* categories */
.cats{left:93px;top:569px;width:232px;height:269px;padding:18px 12px}
.cats ul{list-style:none;margin-top:18px}
.cats li{font-size:10.5px;padding:12px 0;border-bottom:1px solid var(--line);color:#555}
.cats li.on{font-weight:700;color:#222}
.cats li:last-child{border:0}

/* promo */
.promo{left:355px;top:569px;width:752px;height:269px}
.tag-big{position:absolute;left:22px;top:10px;background:var(--orange);color:#fff;font-family:Roboto,sans-serif;font-weight:700;font-size:16px;padding:10px 12px}
.arrows{position:absolute;display:flex;gap:6px}
.arrows span{width:22px;height:22px;background:#e2e2e2}
.promo .info{position:absolute;left:22px;top:90px;width:220px;text-align:center}
.pname{font-weight:700;font-size:11px;color:#222}
.price{color:var(--orange);font-weight:700;font-size:17px;margin-top:12px}
.desc{font-size:9px;line-height:12px;color:var(--muted);margin-top:8px}
.btn-outline{display:inline-block;border:2px solid #ccc;color:#888;font-weight:700;font-size:11px;padding:8px 20px;margin-top:12px}
.ph{background:linear-gradient(135deg,#8a6a4c,#5b4433)}

/* product cards */
.section{padding:0 11px}
.sec-head{display:flex;justify-content:space-between;align-items:center;height:52px}
.filters{font-size:10.5px;color:var(--muted)}
.filters b{color:#555;font-weight:600}
.cards{display:flex;gap:28px}
.card{width:224px;height:314px;border:1px solid var(--line);position:relative;text-align:center}
.card .flag{position:absolute;left:12px;top:8px;font-size:10px;font-weight:700;color:#fff;background:var(--taupe);padding:4px 9px}
.card .flag.o{background:var(--orange)}
.card .img{position:absolute;left:32px;top:30px;width:160px;height:130px}
.card .pname{position:absolute;top:192px;width:100%}
.bar{width:40px;height:3px;background:var(--orange);margin:0 auto}
.card .bar{position:absolute;left:92px;top:212px}
.card .desc{position:absolute;top:220px;left:0;width:100%;padding:0 30px;margin:0}
.pricebox{display:inline-flex;border:1px solid #ccc;height:32px}
.pricebox span{color:var(--orange);font-weight:700;font-size:13px;padding:0 22px;display:flex;align-items:center}
.pricebox i{width:32px;background:var(--taupe);display:flex;align-items:center;justify-content:center}
.card .pricebox{position:absolute;left:60px;top:262px}

.newp{left:355px;top:868px;width:752px;height:381px}
.feat{left:355px;top:1277px;width:752px;height:371px}
.viewmore{left:355px;top:1663px;width:752px;height:39px;background:#4e4e4e;color:#fff;font-weight:700;font-size:11px;display:flex;align-items:center;justify-content:center}
.banner{left:355px;top:1730px;width:752px;height:122px;background:linear-gradient(90deg,#a88562 0%,#c7ab88 40%,#6a4a30 70%,#4a3222 100%)}
.banner-copy{position:absolute;right:30px;top:26px;text-align:right;color:#fff}
.banner-copy h2{font-family:"Open Sans",sans-serif;font-weight:700;font-size:26px}
.banner-copy p{font-size:13px}
.banner-copy small{display:block;font-size:11px;font-weight:700;margin-top:14px}

/* sidebar products */
.best{left:93px;top:868px;width:232px;height:511px;padding:18px 12px}
.side-item{text-align:center}
.side-item .img{width:140px;height:100px;margin:0 auto}
.side-item .pname{margin-top:12px}
.side-item .bar{margin-top:8px}
.side-item .desc{padding:0 10px}
.side-item .pricebox{margin-top:12px}
.special{left:93px;top:1404px;width:232px;height:388px;padding:18px 12px}

/* blog row */
.blogrow{left:93px;top:1878px;width:1016px;height:356px;display:flex;padding:14px 14px}
.col-blog{width:306px;position:relative}
.col-blog .post{padding:14px 0 10px;border-bottom:1px solid var(--line)}
.col-blog .post:last-child{border:0}
.post h4{font-size:10px;font-weight:700}
.post .date{font-size:9px;color:var(--muted);margin:6px 0 12px}
.post p{font-size:8.5px;line-height:12px;color:#555}
.post .more{font-size:8.5px;margin-top:10px;display:block}
.col-tweets{width:300px;margin-left:34px}
.tweet{display:flex;gap:22px;padding:18px 0 14px;border-bottom:1px solid var(--line)}
.tweet:last-child{border:0}
.tweet .dot{flex:none;width:40px;height:40px;border-radius:50%;background:var(--orange);margin-top:4px}
.tweet p{font-size:8.5px;line-height:12px;color:#555}
.tweet b{color:#222}
.tweet em{font-style:normal;color:var(--orange)}
.tweet small{display:block;font-size:8px;margin-top:8px}
.col-video{width:312px;margin-left:34px}
.video{margin-top:16px;width:312px;height:284px;background:linear-gradient(135deg,#d9d6d0,#8f8a80 60%,#5a4a3c);position:relative}
.video .play{position:absolute;left:131px;top:117px}

.strip{left:93px;top:2257px;width:1016px;height:35px;background:var(--white)}

/* footer */
.footer{left:0;top:2298px;width:1200px;height:222px;background:linear-gradient(90deg,var(--wood) 0%,#6a4c37 50%,var(--wood) 100%);color:#f1e8df}
.fcol{position:absolute;top:38px}
.fcol h5{font-size:12px;font-weight:700;margin-bottom:14px;color:#fff}
.fcol li{list-style:none;font-size:10.5px;line-height:24px}
.fcol p{font-size:10.5px}
.nl{display:flex;margin-top:42px}
.nl span{width:180px;height:32px;border:1px solid #fff;font-size:10px;display:flex;align-items:center;justify-content:center}
.nl b{width:66px;height:32px;background:#fff;color:#222;font-size:11px;display:flex;align-items:center;justify-content:center}
.socials{display:flex;gap:7px}
.socials i{width:20px;height:20px;border-radius:50%;background:#fff}
.pay{display:flex;gap:8px;margin-top:10px}
.pay i{width:28px;height:16px;background:#fff}
.bottombar{left:0;top:2520px;width:1200px;height:65px;background:var(--wood-dark);color:#eee;font-size:11px;display:flex;align-items:center;justify-content:space-between;padding:0 93px}
.bottombar nav{display:flex;gap:22px}
</style>
</head>
<body>

<div class="abs topbar">
  <span>Tomas Ridley, welcome to our online store!</span>
  <div class="links"><span>Setting ▾</span><span>My Account ▾</span><span>Cart: 0 item</span></div>
</div>

<header class="abs header">
  <div class="brand"><span class="mark"></span>loma vereda</div>
  <nav class="nav"><a>HOME</a><a>CATEGORIES</a><a>ABOUT US</a><a>FAQs</a><a>CONTACT US</a></nav>
  <div class="search">search your item here
    <svg width="12" height="12" viewBox="0 0 12 12"><circle cx="5" cy="5" r="3.6" fill="none" stroke="#777" stroke-width="1.4"/><line x1="7.6" y1="7.6" x2="11" y2="11" stroke="#777" stroke-width="1.4"/></svg>
  </div>
</header>

<section class="abs hero" role="img" aria-label="Bedroom with a made bed, wooden bedside tables and a warm stone wall">
  <div class="hero-copy">
    <h1>LOREM IPSUMEI</h1>
    <hr>
    <p>aspernatur magni quasi aperiam aut veniatis beatae eos aut voluptas doloremque perspiciatis error natus nulla aut eaque inventore quae consequuntur quis ipsa aspernatur iste at</p>
    <a class="btn-light">VIEW MORE</a>
  </div>
</section>

<aside class="abs box cats">
  <div class="box-title">SHOP BY CATEGORY</div>
  <ul>
    <li>VINTAGE FURNITURE</li>
    <li class="on">RATTAN SET OUTDOOR AND INDOOR</li>
    <li>LAMPS AND</li>
    <li>WOODEN WALL DECOR</li>
  </ul>
</aside>

<section class="abs box promo">
  <div class="tag-big">PROMO OF THE MONTH</div>
  <div class="arrows" style="left:682px;top:10px"><span></span><span></span></div>
  <div class="info">
    <div class="pname">VOLUPTATEM FUGIT AUT</div>
    <div class="price">$380.00</div>
    <div class="desc">ut rerum sit ipsam quasi voluptates eum dolor sint et dolorem quae eaque</div>
    <a class="btn-outline">READ MORE</a>
  </div>
  <div class="ph" role="img" aria-label="Small painted wooden cabinet with an open glass door" style="position:absolute;left:334px;top:17px;width:323px;height:232px"></div>
</section>

<aside class="abs box best">
  <div class="box-title">BEST SELLER</div>
  <div class="side-item" style="margin-top:30px">
    <div class="img ph" role="img" aria-label="Round rattan dining set"></div>
    <div class="pname">VOLUPTATEM FUGIT AUT</div><div class="bar"></div>
    <div class="pricebox"><span>$856.00</span><i><svg width="14" height="12" viewBox="0 0 14 12"><path d="M0 1h3l2 7h7l1.5-5H4" fill="none" stroke="#fff" stroke-width="1.5"/><circle cx="6" cy="10.5" r="1.2" fill="#fff"/><circle cx="11" cy="10.5" r="1.2" fill="#fff"/></svg></i></div>
  </div>
  <div class="side-item" style="margin-top:34px">
    <div class="img ph" role="img" aria-label="Painted vintage wooden chest"></div>
    <div class="pname">VOLUPTATEM FUGIT AUT</div><div class="bar"></div>
    <div class="pricebox"><span>$856.00</span><i><svg width="14" height="12" viewBox="0 0 14 12"><path d="M0 1h3l2 7h7l1.5-5H4" fill="none" stroke="#fff" stroke-width="1.5"/><circle cx="6" cy="10.5" r="1.2" fill="#fff"/><circle cx="11" cy="10.5" r="1.2" fill="#fff"/></svg></i></div>
  </div>
</aside>

<aside class="abs box special">
  <div class="box-title">SPECIAL OFFER</div>
  <div class="arrows" style="left:162px;top:14px"><span></span><span></span></div>
  <div class="side-item" style="margin-top:26px">
    <div class="img ph" role="img" aria-label="Tall distressed painted cupboard" style="width:100px;height:200px"></div>
    <div class="pname">VOLUPTATEM FUGIT AUT</div><div class="bar"></div>
    <div class="desc">ut rerum sit ipsam quasi voluptates dolorem quia aut eaque</div>
    <div class="pricebox"><span>$856.00</span><i><svg width="14" height="12" viewBox="0 0 14 12"><path d="M0 1h3l2 7h7l1.5-5H4" fill="none" stroke="#fff" stroke-width="1.5"/><circle cx="6" cy="10.5" r="1.2" fill="#fff"/><circle cx="11" cy="10.5" r="1.2" fill="#fff"/></svg></i></div>
  </div>
</aside>

<section class="abs box newp section">
  <div class="sec-head"><div class="box-title">NEW PRODUCT</div>
    <div class="filters">Vintage Furniture &nbsp;|&nbsp; <b>Rattan Set Outdoor and Indoor</b> &nbsp;|&nbsp; Lamps &nbsp;|&nbsp; Wooden Wall Decor</div></div>
  <div class="cards">
    <div class="card"><span class="flag">NEW</span><div class="img ph" role="img" aria-label="Painted vintage chest of drawers"></div><div class="pname">VOLUPTATEM FUGIT AUT</div><div class="bar"></div><div class="desc">ut rerum sit ipsam quasi voluptates dolorem quia aut eaque</div><div class="pricebox"><span>$856.00</span><i><svg width="14" height="12" viewBox="0 0 14 12"><path d="M0 1h3l2 7h7l1.5-5H4" fill="none" stroke="#fff" stroke-width="1.5"/><circle cx="6" cy="10.5" r="1.2" fill="#fff"/><circle cx="11" cy="10.5" r="1.2" fill="#fff"/></svg></i></div></div>
    <div class="card"><span class="flag o">10%</span><div class="img ph" role="img" aria-label="Painted wooden coffee table chest"></div><div class="pname">VOLUPTATEM FUGIT AUT</div><div class="bar"></div><div class="desc">ut rerum sit ipsam quasi voluptates dolorem quia aut eaque</div><div class="pricebox"><span>$856.00</span><i><svg width="14" height="12" viewBox="0 0 14 12"><path d="M0 1h3l2 7h7l1.5-5H4" fill="none" stroke="#fff" stroke-width="1.5"/><circle cx="6" cy="10.5" r="1.2" fill="#fff"/><circle cx="11" cy="10.5" r="1.2" fill="#fff"/></svg></i></div></div>
    <div class="card"><span class="flag">NEW</span><div class="img ph" role="img" aria-label="Dark rattan outdoor seating set"></div><div class="pname">VOLUPTATEM FUGIT AUT</div><div class="bar"></div><div class="desc">ut rerum sit ipsam quasi voluptates dolorem quia aut eaque</div><div class="pricebox"><span>$856.00</span><i><svg width="14" height="12" viewBox="0 0 14 12"><path d="M0 1h3l2 7h7l1.5-5H4" fill="none" stroke="#fff" stroke-width="1.5"/><circle cx="6" cy="10.5" r="1.2" fill="#fff"/><circle cx="11" cy="10.5" r="1.2" fill="#fff"/></svg></i></div></div>
  </div>
</section>

<section class="abs box feat section">
  <div class="sec-head"><div class="box-title">FEATURED PRODUCTS</div>
    <div class="filters">Vintage Furniture &nbsp;|&nbsp; Rattan Set Outdoor and Indoor &nbsp;|&nbsp; Lamps &nbsp;|&nbsp; Wooden Wall Decor</div></div>
  <div class="cards">
    <div class="card"><span class="flag">NEW</span><div class="img ph" role="img" aria-label="Round rattan dining set"></div><div class="pname">VOLUPTATEM FUGIT AUT</div><div class="bar"></div><div class="desc">ut rerum sit ipsam quasi voluptates dolorem quia aut eaque</div><div class="pricebox"><span>$856.00</span><i><svg width="14" height="12" viewBox="0 0 14 12"><path d="M0 1h3l2 7h7l1.5-5H4" fill="none" stroke="#fff" stroke-width="1.5"/><circle cx="6" cy="10.5" r="1.2" fill="#fff"/><circle cx="11" cy="10.5" r="1.2" fill="#fff"/></svg></i></div></div>
    <div class="card"><span class="flag">NEW</span><div class="img ph" role="img" aria-label="Painted wooden side table"></div><div class="pname">VOLUPTATEM FUGIT AUT</div><div class="bar"></div><div class="desc">ut rerum sit ipsam quasi voluptates dolorem quia aut eaque</div><div class="pricebox"><span>$856.00</span><i><svg width="14" height="12" viewBox="0 0 14 12"><path d="M0 1h3l2 7h7l1.5-5H4" fill="none" stroke="#fff" stroke-width="1.5"/><circle cx="6" cy="10.5" r="1.2" fill="#fff"/><circle cx="11" cy="10.5" r="1.2" fill="#fff"/></svg></i></div></div>
    <div class="card"><span class="flag">NEW</span><div class="img ph" role="img" aria-label="Table lamp with a cream shade and brass stand" style="background:linear-gradient(180deg,#f3ddb0,#c9a253)"></div><div class="pname">VOLUPTATEM FUGIT AUT</div><div class="bar"></div><div class="desc">ut rerum sit ipsam quasi voluptates dolorem quia aut eaque</div><div class="pricebox"><span>$856.00</span><i><svg width="14" height="12" viewBox="0 0 14 12"><path d="M0 1h3l2 7h7l1.5-5H4" fill="none" stroke="#fff" stroke-width="1.5"/><circle cx="6" cy="10.5" r="1.2" fill="#fff"/><circle cx="11" cy="10.5" r="1.2" fill="#fff"/></svg></i></div></div>
  </div>
</section>

<div class="abs viewmore">VIEW MORE ITEMS</div>

<section class="abs banner" role="img" aria-label="Striped outdoor sofas on a wooden terrace">
  <div class="banner-copy"><h2>outside furniture</h2><p>big savings on quality items</p><small>view the collection</small></div>
</section>

<section class="abs box blogrow">
  <div class="col-blog">
    <div class="box-title">LATES FROM BLOG</div>
    <div class="arrows" style="left:252px;top:0"><span></span><span></span></div>
    <div class="post" style="margin-top:6px">
      <h4>LOREM IPSUM DOLOR SIT AMET REM EOS</h4><div class="date">May 16, 2014</div>
      <p>Lorem ipsum dolor sit amet voluptatem fugit aut illo omnis explicabo nemo enim ipsam quasi illo dolores voluptatem doloremque perspiciatis beatae magni architecto velit nihil aspernatur magni quasi iste ut quo aut eaque inventore aut quae consequuntur quis ipsa</p>
      <a class="more">read more</a>
    </div>
    <div class="post">
      <h4>LOREM IPSUM DOLOR SIT AMET REM EOS</h4><div class="date">May 16, 2014</div>
      <p>Lorem ipsum dolor sit amet voluptatem fugit aut illo omnis explicabo nemo enim ipsam quasi illo dolores voluptatem doloremque perspiciatis beatae magni architecto velit nihil aspernatur magni quasi iste ut quo aut eaque inventore aut quae consequuntur quis ipsa</p>
      <a class="more">read more</a>
    </div>
  </div>
  <div class="col-tweets">
    <div class="box-title">TWEETS</div>
    <div class="tweet"><i class="dot"></i><div><p><b>Ned Farrow</b> <em>@nedfarrow</em><br>Lorem ipsum dolor sit amet voluptatem fugit aut illo omnis explicabo ipsa nemo enim ipsam</p><small>retweeted by <b>Lena Ward</b></small></div></div>
    <div class="tweet"><i class="dot"></i><div><p><b>Ned Farrow</b> <em>@nedfarrow</em><br>Lorem ipsum dolor sit amet voluptatem fugit aut illo omnis explicabo ipsa nemo enim ipsam</p><small>retweeted by <b>Lena Ward</b></small></div></div>
    <div class="tweet"><i class="dot"></i><div><p><b>Ned Farrow</b> <em>@nedfarrow</em><br>Lorem ipsum dolor sit amet voluptatem fugit aut illo omnis explicabo ipsa nemo enim ipsam</p><small>retweeted by <b>Lena Ward</b></small></div></div>
  </div>
  <div class="col-video">
    <div class="box-title">WATCH OUR VIDEO</div>
    <div class="video" role="img" aria-label="Living room with a white sofa and a rustic wooden coffee table">
      <svg class="play" width="50" height="50" viewBox="0 0 50 50"><circle cx="25" cy="25" r="25" fill="#fff"/><path d="M20 15l15 10-15 10z" fill="#222"/></svg>
    </div>
  </div>
</section>

<div class="abs strip"></div>

<footer class="abs footer">
  <div class="fcol" style="left:93px"><h5>COMPANY</h5><ul><li>Search</li><li>About</li><li>News</li><li>Retailers</li><li>Contact Us</li></ul></div>
  <div class="fcol" style="left:265px"><h5>SHIPPING</h5><ul><li>Shipping Fee</li><li>Order and Returns</li><li>Track Order</li><li>Search Term</li><li>Site Map</li></ul></div>
  <div class="fcol" style="left:439px"><h5>FAQs</h5><ul><li>Customers Service</li><li>Privacy Policy</li><li>Term and Use</li><li>My Account</li><li>Others</li></ul></div>
  <div class="fcol" style="left:612px"><h5>NEWS &amp; UPDATES</h5><p>Sign up to get the latest on sales, new releases and more …</p>
    <div class="nl"><span>enter your email here</span><b>SIGN UP</b></div></div>
  <div class="fcol" style="left:958px"><h5>FOLLOW US NOW</h5><div class="socials"><i></i><i></i><i></i><i></i><i></i></div>
    <h5 style="margin-top:26px">PAYMENT METHOD</h5><div class="pay"><i></i><i></i><i></i><i></i></div></div>
</footer>

<div class="abs bottombar">
  <span>© 2014 <b>Your Company</b></span>
  <nav><a>About us</a><a>privacy policy</a><a>terms and use</a><a>Careers</a><a>Countries</a><a>contact us</a></nav>
</div>

</body>
</html>
```